professional business card design

Business card design. Photos have been uploaded and i am open to the designer choosing which photos to use. Would like the card to be mostyly in a grey scale design with black, whites, silver & grey colours. I have added copy of our flyer as would like on the back side of card our services to be listed. Do not use any bright colurs such as blue red green or yellow. i need to be able to edit the phone number and naem in the final card design submitted.

Target Market(s)

Clients

Industry/Entity Type

earhmovibng and transport

Contact Information for Business Card

Director Name, address, email, phone number and services

Colors

Designer to choose only greyscale colors for use in the design.

Requirements
Should not have
• no yellow, red, blue or green

```html
<!DOCTYPE html>
<html lang="en">
<head>
<meta charset="UTF-8">
<title>Ridgeline Haulage – Business Card</title>
<link href="https://fonts.googleapis.com/css2?family=Poppins:wght@300;400;600;700&display=swap" rel="stylesheet">
<style>
  :root{
    --backdrop:#121212;
    --card:#2a2a2a;
    --card-edge:#3a3a3a;
    --text-main:#e9e9e9;
    --text-soft:#bdbdbd;
    --rule:#5a5a5a;
    --silver:#cfcfcf;
    --white:#ffffff;
  }
  *{margin:0;padding:0;box-sizing:border-box;}
  html,body{width:1200px;height:820px;overflow:hidden;}
  body{
    background:var(--backdrop);
    font-family:"Poppins",sans-serif;
    color:var(--text-main);
    display:flex;align-items:center;justify-content:center;gap:40px;
  }
  .card{
    position:relative;width:560px;height:320px;
    background:var(--card);
    border:1px solid var(--card-edge);
    border-radius:4px;
    overflow:hidden;
  }

  /* Front */
  .brand{
    position:absolute;top:70px;left:220px;right:24px;
    text-align:center;
    font-weight:600;font-size:28px;letter-spacing:.5px;color:var(--silver);
    white-space:nowrap;
  }
  .brand-rule{
    position:absolute;top:132px;left:250px;right:24px;
    height:1px;background:var(--rule);
  }
  .person{position:absolute;left:32px;bottom:30px;width:270px;}
  .person-name{font-weight:600;font-size:18px;letter-spacing:.5px;color:var(--silver);line-height:1.15;}
  .person-role{font-weight:300;font-size:14px;color:var(--text-soft);margin-top:2px;}
  .person-rule{height:1px;background:var(--rule);margin:10px 0;}
  .contact-list{list-style:none;}
  .contact-list li{display:flex;align-items:center;gap:8px;font-weight:300;font-size:14px;line-height:1.45;color:var(--text-main);white-space:nowrap;}
  .contact-list svg{width:13px;height:13px;flex:none;}
  .address{
    position:absolute;right:30px;top:184px;text-align:right;
    font-weight:300;font-size:14px;line-height:1.4;color:var(--text-main);
  }

  /* Back */
  .services{position:absolute;left:30px;top:30px;width:300px;}
  .services-title{font-weight:700;font-size:16px;letter-spacing:.3px;margin-bottom:6px;}
  .services-list{list-style:none;}
  .services-list li{
    position:relative;padding-left:14px;
    font-weight:300;font-size:12px;line-height:16px;color:var(--text-main);white-space:nowrap;
  }
  .services-list li::before{
    content:"";position:absolute;left:0;top:5px;width:7px;height:7px;border-radius:50%;background:var(--text-main);
  }
  .truck-photo{
    position:absolute;right:0;top:40px;width:220px;height:196px;
    background:linear-gradient(160deg,#3a3a3a 0%,#8d8d8d 35%,#d9d9d9 55%,#7a6a58 80%,#2a2a2a 100%);
  }
  .closing{position:absolute;left:30px;right:20px;bottom:22px;}
  .closing-note{font-weight:300;font-size:12px;color:var(--text-main);}
  .closing-call{font-weight:700;font-size:13.5px;color:var(--white);margin-top:1px;white-space:nowrap;}
</style>
</head>
<body>

  <section class="card card-front">
    <div class="brand">Ridgeline Haulage</div>
    <div class="brand-rule"></div>

    <div class="person">
      <div class="person-name">MARCUS REID</div>
      <div class="person-role">Managing Director</div>
      <div class="person-rule"></div>
      <ul class="contact-list">
        <li>
          <svg viewBox="0 0 24 24" fill="none" stroke="#e9e9e9" stroke-width="2"><path d="M5 3h4l2 5-3 2a12 12 0 0 0 6 6l2-3 5 2v4a2 2 0 0 1-2 2A17 17 0 0 1 3 5a2 2 0 0 1 2-2z"/></svg>
          044-987 650 312
        </li>
        <li>
          <svg viewBox="0 0 24 24" fill="none" stroke="#e9e9e9" stroke-width="2"><rect x="2" y="5" width="20" height="14"/><path d="M2 5l10 8 10-8"/></svg>
          info@ridgelinehaulage.com
        </li>
        <li>
          <svg viewBox="0 0 24 24" fill="none" stroke="#e9e9e9" stroke-width="2"><circle cx="12" cy="12" r="10"/><path d="M2 12h20M12 2c3 3 3 17 0 20M12 2c-3 3-3 17 0 20"/></svg>
          www.ridgelinehaulage.com
        </li>
      </ul>
    </div>

    <div class="address">18 Quarry Road, Kalgoorlie<br>6430, Australia</div>
  </section>

  <section class="card card-back">
    <div class="services">
      <h2 class="services-title">OUR SERVICES</h2>
      <ul class="services-list">
        <li>Over size loads/hot shot loads</li>
        <li>Heavy vehicle recovery services</li>
        <li>Potable water deliveries</li>
        <li>Road building/maintenance</li>
        <li>Earthworks</li>
        <li>Sand &amp; metal supply &amp; cartage</li>
        <li>Road train tippers</li>
        <li>Road train tankers</li>
        <li>Road train flat tops</li>
        <li>Drop deck trailers</li>
        <li>Mine site accredited</li>
        <li>Equipment &amp; operators</li>
      </ul>
    </div>

    <div class="truck-photo" role="img" aria-label="Photo of a road train truck, front view"></div>

    <div class="closing">
      <p class="closing-note">we offer a large range of services not listed.</p>
      <p class="closing-call">So call us today for a personalised quote to suit your needs.</p>
    </div>
  </section>

</body>
</html>
```